Marketing Flyer for Ashford Hollow Storage Climate Control Units

We are looking for a professional looking Marketing Flyer to advertise for our Climate Control Self Storage Units. Incorporate photos and our LOGO into the marketing flyer. See our website: AshfordHollowstorage.example
Updates

Marketing Flyer for our Self Storage Climate Control Units at Ashford Hollow Storage in Waynesville, NC

Want more designers to have a chance to submit entries.

Target Market(s)

Self Storage Facility Renters

Industry/Entity Type

Self Storage Facility

Font styles to use
Other font styles liked:
• Montserrat Font is what was used for our LOGO and would like to maintain consistency of Font on the Flyer

Colors
0054AA
0677BA
7BADD7
CADEEF
E8F1F8

Requirements
Must have
• Need to have LOGO in the Flyer and photos of the Climate Control Units

```html
<!DOCTYPE html>
<html lang="en">
<head>
<meta charset="utf-8">
<title>Ashford Hollow Storage Flyer</title>
<link href="https://fonts.googleapis.com/css2?family=Montserrat:wght@400;500;600;700&display=swap" rel="stylesheet">
<style>
:root{
  --navy:#1c1a52;
  --white:#ffffff;
  --ink:#222230;
  --page:#e9ebee;
  --sky:#7badd7;
  --sky-light:#cadeef;
  --brick:#9a5a3e;
  --brick-dark:#6e3d2a;
  --unit-blue:#0054aa;
}
*{margin:0;padding:0;box-sizing:border-box}
html,body{width:1200px;height:2824px;overflow:hidden;background:var(--page)}
body{font-family:'Montserrat',sans-serif;position:relative}
.flyer{position:absolute;left:36px;top:611px;width:940px;height:1335px;background:var(--white);transform:scale(1.2);transform-origin:0 0;overflow:hidden;box-shadow:0 4px 14px rgba(0,0,0,.25)}
.hero{position:absolute;left:0;top:0;width:940px;height:430px}
.brand-box{position:absolute;left:45px;top:2px;width:226px;height:141px;background:var(--white);display:flex;flex-direction:column;align-items:center;justify-content:center;gap:4px}
.brand-mark{width:40px;height:40px;background:var(--navy);margin-bottom:8px}
.brand-name{font-family:'Montserrat',sans-serif;font-weight:600;color:var(--navy);font-size:19px;line-height:1.05;text-align:center;letter-spacing:.5px}
.copy{position:absolute;left:45px;width:431px;color:var(--ink)}
.copy h2{font-size:18.5px;font-weight:600;color:var(--navy);line-height:22px}
.copy p{font-size:13.2px;line-height:17px;text-align:justify;margin-top:12px}
.features{position:absolute;left:531px;top:435px;width:397px;height:560px;background:var(--navy);color:var(--white)}
.features-tab{position:absolute;left:0;top:0}
.features-title{position:absolute;left:42px;top:5px;width:315px;text-align:center;font-size:20px;font-weight:600;color:var(--navy)}
.features-intro{position:absolute;left:18px;top:60px;width:361px;font-size:13.4px;line-height:17px;text-align:justify}
.features-list{position:absolute;left:30px;top:156px;list-style:none}
.features-list li{font-size:13.6px;font-weight:600;line-height:25.3px}
.features-list li::before{content:"•";margin-right:9px}
.sizes{position:absolute;left:573px;top:910px;width:313px;height:152px;background:var(--white);text-align:center;color:var(--navy);font-weight:600;font-size:27px;line-height:43px;padding-top:18px}
.units{position:absolute;left:543px;top:1065px}
.website{position:absolute;left:531px;top:1226px;width:397px;text-align:center;font-size:22px;font-weight:600;color:var(--navy)}
.footer{position:absolute;left:0;top:1270px}
.footer-info{position:absolute;left:350px;top:1283px;width:340px;text-align:center;color:var(--white)}
.footer-name{font-size:16px;font-weight:600;line-height:18px}
.footer-address{font-size:12.6px;line-height:16px}
.footer-phone{position:absolute;left:710px;top:1290px;font-size:26px;font-weight:600;color:var(--white)}
</style>
</head>
<body>
<main class="flyer">
  <svg class="hero" width="940" height="430" viewBox="0 0 940 430">
    <defs>
      <linearGradient id="siteGrad" x1="0" y1="0" x2="0" y2="1">
        <stop offset="0" stop-color="#4c8fd0"/>
        <stop offset=".45" stop-color="#8fbfe3"/>
        <stop offset=".62" stop-color="#6e9a52"/>
        <stop offset=".78" stop-color="#9a5a3e"/>
        <stop offset="1" stop-color="#8a8c90"/>
      </linearGradient>
      <linearGradient id="entryGrad" x1="0" y1="0" x2="1" y2="1">
        <stop offset="0" stop-color="#a3603f"/>
        <stop offset=".55" stop-color="#8a4c34"/>
        <stop offset="1" stop-color="#b89a88"/>
      </linearGradient>
    </defs>
    <g role="img" aria-label="Photo of the storage building with the padlock-shaped entrance sign">
      <rect x="0" y="0" width="560" height="430" fill="url(#siteGrad)"/>
    </g>
    <polygon points="526,0 940,0 940,430 521,430 414,225" fill="var(--white)"/>
    <g role="img" aria-label="Photo of the brick office entrance with glass door and bench">
      <polygon points="540,0 940,0 940,430 535,430 428,225" fill="url(#entryGrad)"/>
    </g>
  </svg>

  <div class="brand-box">
    <div class="brand-mark"></div>
    <div class="brand-name">ASHFORD HOLLOW<br>STORAGE</div>
  </div>

  <section class="copy" style="top:450px">
    <h2>Storage Units and Vehicle<br>Storage in Waynesville, NC</h2>
    <p>When you need a bit more room for all the items you need for your household or business, Ashford Hollow Storage, powered by Birchline Storage Management, can help you get some square footage. Our convenient Waynesville self-storage facility is located on Lantern Street, near Orchard Avenue. Along with a variety of storage unit sizes and features, we even offer outdoor parking storage, suitable for keeping your extra recreational vehicles in between Smoky Mountain adventures, lake trips, family road trips, and more.</p>
  </section>
  <section class="copy" style="top:680px">
    <h2 style="text-align:justify;text-align-last:left">Waynesville Storage Facility Near Orchard Avenue</h2>
    <p>Our self-storage in Waynesville, NC, is located conveniently close to Orchard Avenue, allowing for hassle-free navigation to your storage space. We’re also close to many of your other necessary stops around town, including PartsDepot, Ridgeway Bank, Summit Credit Union, Marco’s Family Pizza &amp; Pasta Restaurant, Keller Auto Parts, and the Hollow Creek Plaza shopping center. Whether you’re looking for a storage unit to supplement the space in your living or working space, you’ll find Ashford Hollow Storage nearby.</p>
  </section>
  <section class="copy" style="top:910px">
    <h2>Drive-Up Access Storage in Waynesville</h2>
    <p>Choose one of our drive-up storage units and store even your largest items with ease! With drive-up access storage, you’ll be able to pull your personal or moving vehicles directly up to your Waynesville self-storage unit and get your items moved in or out with ease. Have lighter items that you just need to access as quickly as possible? Drive-up storage units are still a great choice!</p>
  </section>
  <section class="copy" style="top:1085px">
    <h2>Waynesville Climate-Controlled Storage</h2>
    <p>Ashford Hollow Storage is adding new climate-controlled storage units in the summer of 2023. With the variable North Carolina weather, climate-controlled storage is a great option for keeping your sensitive belongings like files and furniture away from the elements. This is especially important when storing items long-term through seasonal changes. Our climate-controlled storage units are conveniently available in several sizes to help meet all of your storage needs.</p>
  </section>

  <aside class="features">
    <svg class="features-tab" width="397" height="40" viewBox="0 0 397 40">
      <polygon points="50,0 357,0 340,36 30,36" fill="var(--white)"/>
    </svg>
    <h3 class="features-title">Features &amp; Amenities</h3>
    <p class="features-intro">Every storage feature is designed from scratch against standards forged from years of experience in the self storage industry. The result is a high quality consistent customer experience you can count on.</p>
    <ul class="features-list">
      <li>24/7 Access</li>
      <li>All Major Credit Cards Accepted</li>
      <li>Auto Pay</li>
      <li>Climate Controlled Units</li>
      <li>Contactless Rental and Payment</li>
      <li>Covered Vehicle / Boat / RV Parking</li>
      <li>Drive Up Access</li>
      <li>Drive-Up Units</li>
      <li>Ground Floor Units</li>
      <li>Outdoor Parking</li>
      <li>Phone Support</li>
      <li>Trailer Storage</li>
    </ul>
  </aside>

  <div class="sizes">All Sizes<br>Small &nbsp;|&nbsp; Medium &nbsp;|<br>Large Parking</div>

  <svg class="units" width="372" height="132" viewBox="0 0 372 132">
    <defs>
      <linearGradient id="hallGrad" x1="0" y1="0" x2="1" y2="0">
        <stop offset="0" stop-color="#e8f1f8"/>
        <stop offset=".5" stop-color="#cadeef"/>
        <stop offset="1" stop-color="#0054aa"/>
      </linearGradient>
      <linearGradient id="doorGrad" x1="0" y1="0" x2="1" y2="1">
        <stop offset="0" stop-color="#0677ba"/>
        <stop offset="1" stop-color="#0054aa"/>
      </linearGradient>
    </defs>
    <g fill="none" stroke="var(--navy)" stroke-width="1.2">
      <polygon points="63,2 120,34 120,98 63,130 6,98 6,34"/>
      <polygon points="186,2 243,34 243,98 186,130 129,98 129,34"/>
      <polygon points="309,2 366,34 366,98 309,130 252,98 252,34"/>
    </g>
    <polygon role="img" aria-label="Photo of a climate-controlled hallway with blue unit doors" points="63,9 114,38 114,94 63,123 12,94 12,38" fill="url(#hallGrad)"/>
    <polygon role="img" aria-label="Photo of an indoor corridor lined with blue storage doors" points="186,9 237,38 237,94 186,123 135,94 135,38" fill="url(#hallGrad)"/>
    <polygon role="img" aria-label="Photo of a blue roll-up storage unit door" points="309,9 360,38 360,94 309,123 258,94 258,38" fill="url(#doorGrad)"/>
  </svg>

  <div class="website">AshfordHollowstorage.example</div>

  <svg class="footer" width="940" height="65" viewBox="0 0 940 65">
    <rect x="0" y="36" width="370" height="9" fill="var(--navy)"/>
    <polygon points="378,5 940,5 940,65 340,65" fill="var(--navy)"/>
  </svg>
  <div class="footer-info">
    <div class="footer-name">Ashford Hollow Storage</div>
    <div class="footer-address">42 West Lantern St, Waynesville, NC 28786</div>
  </div>
  <div class="footer-phone">(555) 014-2290</div>
</main>
</body>
</html>
```